Bramblewood Card Company Business Cards

We are a trading card store with Glimmorax, sports and other TCG cards, we need a business card design that encompasses a clean cut, modern style with a retro flare. website is bramblewoodcardco.com for reference. Can utilize a comic book era feel or a more modern outdoor feel to utilize the "Pacific Northwest" elements of tress, mountains, etc.

Industry/Entity Type

Trading cards and collectibles

Contact Information for Business Card

business name, email address, phone number, name, owner job title

Font styles to use
Sans Serif

```html
<!DOCTYPE html>
<html lang="en">
<head>
<meta charset="utf-8">
<title>Bramblewood Card Company – Business Cards</title>
<link rel="stylesheet" href="https://fonts.googleapis.com/css2?family=Montserrat:wght@700&family=Roboto:wght@400;500&display=swap">
<style>
  :root {
    --backdrop: #2b2b2b;
    --card-grey: #6e6e6e;
    --card-white: #ffffff;
    --ink-grey: #666666;
    --ink-soft: #8a8a8a;
    --accent-cyan: #1cb3d9;
    --rule: #d9d9d9;
  }
  * { margin: 0; padding: 0; box-sizing: border-box; }
  html, body {
    width: 1200px;
    height: 689px;
    overflow: hidden;
    background: var(--backdrop);
    font-family: "Roboto", Arial, sans-serif;
  }
  .canvas {
    width: 1200px;
    height: 689px;
    display: flex;
    align-items: center;
    justify-content: center;
    gap: 48px;
  }
  .card {
    position: relative;
    width: 525px;
    height: 300px;
    border-radius: 22px;
    overflow: hidden;
  }
  .card--front {
    background: var(--card-grey);
    display: flex;
    align-items: center;
    justify-content: center;
  }
  .brand-mark {
    display: flex;
    align-items: center;
    gap: 12px;
    font-family: "Montserrat", Arial, sans-serif;
    font-weight: 700;
    text-transform: uppercase;
    letter-spacing: 0.04em;
    line-height: 1.1;
  }
  .brand-mark__square {
    width: 18px;
    height: 18px;
    flex: none;
  }
  .card--front .brand-mark { color: var(--card-white); font-size: 26px; }
  .card--front .brand-mark__square { background: var(--accent-cyan); }

  .card--back { background: var(--card-white); }
  .card--back .brand-mark {
    position: absolute;
    top: 44px;
    right: 40px;
    color: var(--ink-grey);
    font-size: 17px;
    text-align: right;
  }
  .card--back .brand-mark__square { background: var(--accent-cyan); width: 14px; height: 14px; }
  .divider {
    position: absolute;
    left: 230px;
    right: 40px;
    top: 138px;
    height: 1px;
    background: var(--rule);
  }
  .contact {
    position: absolute;
    left: 40px;
    right: 40px;
    bottom: 36px;
  }
  .contact__name {
    color: var(--accent-cyan);
    font-weight: 500;
    font-size: 26px;
    line-height: 1.1;
  }
  .contact__title {
    color: var(--ink-soft);
    font-size: 13px;
    margin-bottom: 14px;
  }
  .contact__details {
    display: flex;
    align-items: center;
    gap: 9px;
    color: var(--ink-grey);
    font-size: 12px;
    white-space: nowrap;
  }
  .contact__details span { flex: none; }
  .contact__sep { color: var(--ink-soft); }
</style>
</head>
<body>
  <main class="canvas">
    <section class="card card--front" aria-label="Card front">
      <div class="brand-mark">
        <span class="brand-mark__square"></span>
        <span>Bramblewood<br>Card Company</span>
      </div>
    </section>

    <section class="card card--back" aria-label="Card back">
      <div class="brand-mark">
        <span class="brand-mark__square"></span>
        <span>Bramblewood<br>Card Company</span>
      </div>
      <div class="divider"></div>
      <div class="contact">
        <p class="contact__name">Avery Lund</p>
        <p class="contact__title">President</p>
        <p class="contact__details">
          <span>555-014-2298</span>
          <span class="contact__sep">|</span>
          <span>info@bramblewoodcardco.com</span>
          <span class="contact__sep">|</span>
          <span>www.bramblewoodcardco.com</span>
        </p>
      </div>
    </section>
  </main>
</body>
</html>
```